Kestrel Baseball & Softball Camp 2017

Design a flyer that will promote our 2017 summer camp for boys and girls softball.

Weeks of
July 10th - 14th
July 17th - 21st.

Players ages 5 - 11.
Full day = 9:30am - 2:30pm half day = 9:30am - 11:30am.
$295 / full day : $195/ half day

Hosted by "Kestrel Baseball" affiliated with the Harbor Comets Travel Baseball & Softball Club and the Maple Ridge Youth League,

Camp Location MRYL, Route 9C Birch Hollow.

PHone 555-240-7813, email info@kestrelball.example

The color should be "Red white and blue color scheme" with dates and location standing out. Kestrel Logo should be prominent MRYL and Comets smaller and secondary.

Feel free to use stock photo's if available. visit www.harborcomets.example for more pictures and there are links for the 2017 summer camp there with possibly some more information.

Target Market(s)

to catch the eye of parents of players ages 5 - 11 already at little league or shopping in local stores

Colors
ec1f27
0355a3
ffffff

Requirements
Must have
• red white and blue design,
• Kestrel logo and summer camp prominent so it catches the eye and explains what it is right away.
• the comets and maple ridge logo's a the bottom showing the affiliation.
Nice to have
• stock photo's or something showing players having a great time or a beautiful ballpark
Should not have
• to much clutter or hard to figure out what it's for

```html
<!DOCTYPE html>
<html lang="en">
<head>
<meta charset="utf-8">
<title>Kestrel Baseball &amp; Softball – Softball Summer Camp 2017</title>
<link rel="stylesheet" href="https://fonts.googleapis.com/css2?family=Bebas+Neue&family=Oswald:wght@500;600&family=Kaushan+Script&display=swap">
<style>
  :root {
    --red: #ec1f27;
    --deep-red: #c8202a;
    --navy: #1f3566;
    --blue: #0355a3;
    --white: #ffffff;
    --grey: #8a8f99;
  }
  * { margin: 0; padding: 0; box-sizing: border-box; }
  html, body { width: 817px; height: 1200px; overflow: hidden; background: var(--white); }
  .flyer { position: relative; width: 817px; height: 1200px; overflow: hidden; background: var(--white); font-family: 'Oswald', sans-serif; }
  .backdrop { position: absolute; inset: 0; }
  .abs { position: absolute; }

  .brand { left: 38px; top: 70px; display: flex; align-items: center; gap: 10px; }
  .brand-dot { width: 26px; height: 26px; border-radius: 50%; background: var(--blue); }
  .brand-name { font-family: 'Bebas Neue', sans-serif; font-size: 54px; color: var(--deep-red); line-height: 1; }

  .script-softball { left: 58px; top: 300px; font-family: 'Kaushan Script', cursive; font-size: 62px; color: var(--white); transform: rotate(-6deg); }
  .title { left: 50px; top: 392px; font-family: 'Bebas Neue', sans-serif; font-size: 136px; line-height: 1; letter-spacing: 1px; font-weight: 400; }
  .title .summer { color: var(--white); }
  .title .camp { color: var(--deep-red); }
  .year { top: 330px; left: 748px; font-family: 'Bebas Neue', sans-serif; font-size: 56px; color: var(--deep-red); transform: rotate(90deg); transform-origin: left top; }
  .tagline { left: 448px; top: 500px; font-family: 'Kaushan Script', cursive; font-size: 22px; color: var(--white); transform: rotate(-4deg); }

  .weeks { left: 80px; top: 614px; font-family: 'Bebas Neue', sans-serif; font-size: 40px; line-height: 1.0; color: var(--white); }
  .weeks span { display: block; height: 39px; }

  .hosted { left: 416px; top: 592px; font-family: 'Oswald', sans-serif; font-weight: 500; font-size: 11.5px; line-height: 28px; letter-spacing: .5px; color: var(--navy); text-transform: uppercase; }
  .partner { display: flex; align-items: center; gap: 8px; font-family: 'Oswald', sans-serif; font-weight: 600; color: var(--deep-red); text-transform: uppercase; }
  .partner-comets { left: 640px; top: 588px; font-size: 26px; }
  .partner-maple { left: 646px; top: 672px; font-size: 18px; color: var(--navy); }
  .partner-mark { width: 24px; height: 24px; background: var(--navy); border-radius: 50%; }

  .hours { left: 110px; top: 817px; font-family: 'Oswald', sans-serif; font-weight: 500; font-size: 21px; line-height: 33px; color: var(--deep-red); text-transform: uppercase; }
  .cost-label { left: 120px; top: 928px; font-family: 'Kaushan Script', cursive; font-size: 20px; color: var(--navy); }
  .cost { left: 222px; top: 916px; font-family: 'Oswald', sans-serif; font-weight: 500; font-size: 21px; line-height: 33px; color: var(--navy); text-transform: uppercase; }

  .ages { left: 480px; top: 862px; font-family: 'Bebas Neue', sans-serif; font-size: 42px; line-height: 1.1; color: var(--navy); }
  .ages-badge { left: 604px; top: 829px; width: 136px; height: 136px; border-radius: 50%; background: var(--navy); color: var(--white); display: flex; align-items: center; justify-content: center; font-family: 'Oswald', sans-serif; font-weight: 500; font-size: 36px; }

  .register { left: 204px; top: 1038px; font-family: 'Kaushan Script', cursive; font-size: 34px; line-height: 1.1; color: var(--deep-red); transform: rotate(-8deg); }
  .info-head { font-family: 'Kaushan Script', cursive; font-size: 17px; line-height: 22px; color: var(--navy); }
  .info-body { font-family: 'Oswald', sans-serif; font-weight: 500; font-size: 14.5px; line-height: 1.6; color: var(--navy); text-transform: uppercase; margin-top: 6px; }
  .location { left: 372px; top: 1042px; }
  .location .info-body { margin-left: 2px; }
  .contact { left: 585px; top: 1042px; }
</style>
</head>
<body>
<main class="flyer">
  <svg class="backdrop" width="817" height="1200" viewBox="0 0 817 1200">
    <defs>
      <linearGradient id="fieldTone" x1="0" y1="0" x2="0" y2="1">
        <stop offset="0" stop-color="#b9c3c4"/>
        <stop offset="0.35" stop-color="#a59277"/>
        <stop offset="1" stop-color="#c49a6a"/>
      </linearGradient>
      <radialGradient id="ballTone" cx="0.5" cy="0.55" r="0.6">
        <stop offset="0" stop-color="#f2f05a"/>
        <stop offset="0.6" stop-color="#d9d43a"/>
        <stop offset="1" stop-color="#8a5a35"/>
      </radialGradient>
    </defs>
    <polygon points="330,0 817,0 817,540 0,560 0,235" fill="url(#fieldTone)" role="img" aria-label="Photo of a young player in a batting helmet sliding into base as a fielder's glove catches the ball"/>
    <polygon points="0,395 670,312 595,560 0,560" fill="var(--navy)"/>
    <polygon points="0,548 440,492 345,790 0,822" fill="var(--deep-red)"/>
    <line x1="0" y1="580" x2="420" y2="530" stroke="var(--white)" stroke-width="1.5" stroke-dasharray="10 7"/>
    <line x1="345" y1="790" x2="817" y2="752" stroke="var(--grey)" stroke-width="2" stroke-dasharray="7 6"/>
    <rect x="0" y="945" width="190" height="255" fill="url(#ballTone)" role="img" aria-label="Photo of a yellow softball resting beside a leather glove and bat"/>
    <g fill="none" stroke="var(--deep-red)" stroke-width="3">
      <circle cx="80" cy="850" r="13"/>
      <line x1="80" y1="850" x2="80" y2="842"/>
      <line x1="75" y1="832" x2="85" y2="832"/>
    </g>
    <circle cx="188" cy="943" r="15" fill="var(--navy)"/>
    <text x="188" y="951" font-family="Oswald, sans-serif" font-size="20" font-weight="600" fill="var(--white)" text-anchor="middle">$</text>
    <g fill="var(--navy)">
      <circle cx="443" cy="870" r="5"/><rect x="437" y="877" width="12" height="14" rx="2"/><rect x="438" y="890" width="4" height="12"/><rect x="444" y="890" width="4" height="12"/>
      <circle cx="463" cy="870" r="5"/><polygon points="463,877 455,893 471,893"/><rect x="458" y="892" width="4" height="10"/><rect x="464" y="892" width="4" height="10"/>
    </g>
    <path d="M347 1045 a7 7 0 0 1 14 0 c0 6 -7 13 -7 13 s-7 -7 -7 -13z" fill="var(--navy)"/>
    <circle cx="354" cy="1045" r="2.5" fill="var(--white)"/>
    <rect x="562" y="1036" width="13" height="22" rx="3" fill="var(--navy)"/>
    <rect x="565" y="1040" width="7" height="9" fill="var(--white)"/>
  </svg>

  <div class="abs brand"><span class="brand-dot"></span><span class="brand-name">Kestrel</span></div>

  <div class="abs script-softball">softball</div>
  <h1 class="abs title"><span class="summer">SUMMER</span><span class="camp">CAMP</span></h1>
  <div class="abs year">2017</div>
  <div class="abs tagline">for boys and girls</div>

  <div class="abs weeks"><span>WEEKS OF</span><span>JULY 10TH - 14TH</span><span>JULY 17TH - 21ST.</span></div>

  <p class="abs hosted">Hosted by "Kestrel Baseball"<br>Affiliated with the Harbor Comets<br>Travel Baseball &amp; Softball Club and<br>the Maple Ridge Youth League</p>
  <div class="abs partner partner-comets">Comets</div>
  <div class="abs partner partner-maple"><span class="partner-mark"></span>Maple Ridge</div>

  <p class="abs hours">Full day = 9:30am - 2:30pm<br>Half day = 9:30am - 11:30am</p>
  <div class="abs cost-label">Cost:</div>
  <p class="abs cost">$295 / full day<br>$195/ half day</p>

  <div class="abs ages">PLAYERS<br>AGES</div>
  <div class="abs ages-badge">5 - 11</div>

  <div class="abs register">Register<br>today!</div>
  <div class="abs location">
    <div class="info-head">Camp Location:</div>
    <div class="info-body">Camp location MRYL,<br>Route 9C Birch Hollow.</div>
  </div>
  <div class="abs contact">
    <div class="info-head">Contact:</div>
    <div class="info-body">Phone 555-240-7813, email<br>info@kestrelball.example</div>
  </div>
</main>
</body>
</html>
```